Website Design Project for Beauty & Wellness Professionals

As background information, I have a website that is focused on Beauty & Wellness Professionals:
- Job Search (www.lumarinovo.com)
- Business Classifieds (negocios.lumarinovo.com)
- Freelancer Classifieds (freelancer.lumarinovo.com)
- Course Reviews (cursos.lumarinovo.com)

All those websites use standard templates.

I need a DESIGN for the HOME PAGE (no coding) of the Website Platform that consolidates the four platforms under the same design.

Website designs that we like:
- quelvox.com
- brintmoor.com

Target Market(s)

Brazilian Professionals from Beauty & Wellness sector

Industry/Entity Type

Business

Requirements
Must have
• Website designs that we like:
- quelvox.com
- brintmoor.com

```html
<!DOCTYPE html>
<html lang="en">
<head>
<meta charset="utf-8">
<title>Lumarinovo – Find Your Dream Job</title>
<link href="https://fonts.googleapis.com/css2?family=Source+Sans+3:wght@300;400;600;700&display=swap" rel="stylesheet">
<style>
:root{
  --orange:#e0683a;
  --teal:#3aa6c8;
  --teal-light:#6fc6dd;
  --ink:#333;
  --muted:#888;
  --line:#ddd;
  --page:#f4f5f6;
  --footer:#2a2b2d;
  --white:#fff;
}
*{box-sizing:border-box;margin:0;padding:0}
html,body{width:757px;height:1200px;overflow:hidden}
body{position:relative;background:var(--page);font-family:"Source Sans 3",Arial,sans-serif;color:var(--ink)}
.abs{position:absolute}

/* header */
.site-header{left:0;top:0;width:757px;height:70px;background:linear-gradient(#fff,#f3f3f3)}
.brand{left:58px;top:17px;display:flex;align-items:center;gap:8px;color:var(--teal);font-size:22px;font-weight:400}
.brand-dot{width:26px;height:26px;border-radius:50%;background:var(--teal)}
.account{right:70px;top:7px;font-size:9px;color:var(--orange)}
.account span{color:var(--muted);margin:0 5px}
.account .up{color:var(--teal)}
.main-nav{right:64px;top:36px;display:flex;align-items:center;font-size:12.5px;color:#444}
.main-nav a{padding:0 10px;border-left:1px solid var(--line);line-height:14px}
.main-nav a:first-child{border:0}

/* hero */
.hero{left:0;top:70px;width:757px;height:284px;background:linear-gradient(100deg,#8ad6e2 0%,#bfe8ee 30%,#f0d2c0 55%,#e9c5b0 75%,#7fd0de 100%)}
.hero-kicker{left:111px;top:172px;font-size:19px;font-weight:700;color:#fff;text-shadow:0 1px 3px rgba(0,0,0,.35)}
.hero-title{left:110px;top:195px;font-size:32px;font-weight:700;color:#fff;text-shadow:0 1px 4px rgba(0,0,0,.35)}
.search-bar{left:111px;top:244px;width:536px;height:47px;background:rgba(40,40,40,.8);padding:10px 8px;display:flex;gap:6px}
.search-bar .field{background:#fff;height:25px;border-radius:2px;font-size:10px;color:#999;padding:0 11px;display:flex;align-items:center}
.search-bar .select{width:90px;background:#eee;color:#444;justify-content:space-between;padding-right:0}
.search-bar .select i{width:20px;border-left:1px solid #ccc;height:100%;display:flex;align-items:center;justify-content:center;font-style:normal;font-size:8px}
.search-btn{width:71px;height:25px;background:linear-gradient(#6cc4e0,#3f9fc4);color:#fff;font-size:11px;display:flex;align-items:center;justify-content:center;border-radius:2px;margin-left:2px}

/* content card */
.content{left:58px;top:354px;width:640px;height:766px;background:#fff}
.section-title{font-size:15px;font-weight:400;color:#333}
.job-list{list-style:none}
.job{position:relative;height:90px;background:linear-gradient(#fff 70%,#f2f2f2);display:flex;padding-top:6px}
.job-thumb{width:52px;height:52px;border:1px solid #e2e2e2;padding:3px;margin:0 14px 0 10px;background:#fff;flex:none}
.job-thumb div{width:100%;height:100%}
.job-main{width:176px;font-size:10px;line-height:13px}
.job-main h3{font-size:10.5px;font-weight:400;color:var(--orange);line-height:13.5px;margin-bottom:4px}
.job-main p{font-size:7.5px;color:#777;line-height:11px}
.job-place{width:92px;margin-left:10px;border-left:1px solid var(--line);padding-left:16px;height:70px;font-size:10.5px}
.job-place small,.job-date small{display:block;font-size:7.5px;color:#888;line-height:11px;margin-top:2px}
.job-date{border-left:1px solid var(--line);padding-left:12px;height:50px;margin-left:0;font-size:10.5px}
.view-all{left:390px;top:1071px;font-size:8px;color:#444}

/* sidebar */
.vacancies{left:525px;top:376px}
.vacancies h2{font-size:15px;font-weight:400;color:var(--orange);margin-bottom:8px}
.vacancies ul{list-style:none}
.vacancies li{font-size:8.5px;color:#555;height:18.7px;padding-left:11px;position:relative}
.vacancies li::before{content:"";position:absolute;left:0;top:3px;border:3px solid transparent;border-left:3px solid #bbb}
.side-divider{left:505px;top:676px;width:172px;height:1px;background:var(--line)}
.side-rule{left:505px;top:376px;width:1px;height:300px;background:#eee}
.tabs{left:518px;top:690px;display:flex;gap:3px}
.tab{height:21px;padding:0 10px;font-size:9.5px;color:#fff;display:flex;align-items:center}
.tab.active{background:var(--teal-light)}
.tab.alt{background:var(--orange)}
.filter-box{left:518px;top:711px;width:164px;height:94px;border:1px solid var(--line);padding:5px 12px}
.filter-box div{height:18.7px;border-bottom:1px solid #eee;font-size:8.5px;color:#555;display:flex;justify-content:space-between;align-items:center}
.filter-box div:last-child{border:0}
.newsletter{left:518px;top:816px;width:164px;height:90px;border:1px solid var(--line);background:linear-gradient(#fff,#f4f4f4);padding:10px 11px}
.newsletter h2{font-size:12px;font-weight:400;color:var(--teal);margin-bottom:5px}
.newsletter .email{height:17px;border:1px solid #ccc;background:#fff;font-size:7px;color:#666;padding:3px 6px}
.newsletter .subscribe{margin:7px 0 0 auto;width:62px;height:17px;background:var(--orange);color:#fff;font-size:7.5px;display:flex;align-items:center;justify-content:center}
.ad{left:520px;top:923px;width:160px;height:160px;background:linear-gradient(#1f6fb8,#2a82c6 60%,#1d62a6)}

/* footer */
.site-footer{left:0;top:1120px;width:757px;height:80px;background:var(--footer);color:#fff}
.foot-nav{left:62px;top:28px;font-size:9.5px;display:flex}
.foot-nav a{padding:0 5px;border-left:1px solid #ccc;line-height:10px}
.foot-nav a:first-child{border:0;padding-left:0}
.copyright{left:62px;top:47px;font-size:7.5px;color:#999}
.social{right:66px;top:28px;display:flex;gap:4px}
.social span{width:19px;height:19px;border-radius:50%;background:#fff}
</style>
</head>
<body>

<header class="site-header abs">
  <div class="brand abs"><span class="brand-dot"></span>Lumarinovo</div>
  <div class="account abs">Sign In<span>|</span><a class="up">Sign Up</a></div>
  <nav class="main-nav abs">
    <a><svg width="15" height="14" viewBox="0 0 15 14"><path d="M7.5 0 0 7h2v7h4V9h3v5h4V7h2z" fill="#e0683a"/></svg></a>
    <a>Blog</a><a>For Business</a><a>Events &amp; Partners</a><a>About Us</a><a>Contact</a>
  </nav>
</header>

<section class="hero abs" role="img" aria-label="Photo of a woman relaxing during a spa facial treatment">
</section>
<div class="hero-kicker abs">Looking for a Career In Beauty..</div>
<h1 class="hero-title abs">Find Your Dream Job</h1>
<form class="search-bar abs">
  <div class="field select">Jobs<i>▼</i></div>
  <div class="field" style="width:200px">Key tittle or company</div>
  <div class="field" style="width:138px">Locations</div>
  <div class="search-btn">SEARCH</div>
</form>

<main class="content abs"></main>

<section class="abs" style="left:74px;top:376px;width:413px">
  <h2 class="section-title" style="margin:0 0 10px 7px">Featured Job Vacancies</h2>
  <ul class="job-list">
    <li class="job"><div class="job-thumb"><div role="img" aria-label="Portrait photo" style="background:linear-gradient(#5a3a2e,#c99b83)"></div></div>
      <div class="job-main"><h3>Aux. Hairdresser (Escovista) - Santo André (SP)</h3><p>Marta Veloso / Onix Hair and Esthetics - Posted by Marta De Veloso</p></div>
      <div class="job-place">Santo André<small>São Paulo, the Federative Republic of Brazil</small></div>
      <div class="job-date">July 18<small>2013</small></div></li>
    <li class="job"><div class="job-thumb"><div role="img" aria-label="Portrait photo" style="background:linear-gradient(#3a2a24,#d4a78f)"></div></div>
      <div class="job-main"><h3>Manicure - Closest subway Vila Madalena - São Paulo (SP)</h3><p>JR Manicure and Waxing - Posted by jobs</p></div>
      <div class="job-place">Santo André<small>São Paulo, the Federative Republic of Brazil</small></div>
      <div class="job-date">July 18<small>2013</small></div></li>
    <li class="job"><div class="job-thumb"><div role="img" aria-label="Portrait photo" style="background:linear-gradient(#8a5a3e,#e6c6b2)"></div></div>
      <div class="job-main"><h3>Manicure - Jabalpur - São Paulo (SP)</h3><p>Esmalteria Aurora - Unit Jabalpur - Posted by rosa_belmiro</p></div>
      <div class="job-place">Santo André<small>São Paulo, the Federative Republic of Brazil</small></div>
      <div class="job-date">July 18<small>2013</small></div></li>
  </ul>
</section>

<section class="abs" style="left:74px;top:685px;width:413px">
  <h2 class="section-title" style="margin:0 0 10px 7px">Latest Job Vacancies</h2>
  <ul class="job-list">
    <li class="job"><div class="job-thumb"><div role="img" aria-label="Portrait photo" style="background:linear-gradient(#e8e2dc,#d9b6a0)"></div></div>
      <div class="job-main"><h3>Manicure / Pedicure - Grajaú - Rio de Janeiro (RJ)</h3><p>Marta Veloso / Onix Hair and Esthetics - Posted by Marta De Veloso</p></div>
      <div class="job-place">Santo André<small>São Paulo, the Federative Republic of Brazil</small></div>
      <div class="job-date">June 28<small>2013</small></div></li>
    <li class="job"><div class="job-thumb"><div role="img" aria-label="Close-up beauty photo" style="background:linear-gradient(#9fd8de,#e8c1b2)"></div></div>
      <div class="job-main"><h3>Manicure and Pedicure - São Paulo (SP)</h3><p>JR Manicure and Waxing - Posted by jobs</p></div>
      <div class="job-place">Santo André<small>São Paulo, the Federative Republic of Brazil</small></div>
      <div class="job-date">June 22<small>2013</small></div></li>
    <li class="job"><div class="job-thumb"><div role="img" aria-label="Colorful makeup photo" style="background:linear-gradient(135deg,#d8413a,#e7c4a0,#4a8fc4)"></div></div>
      <div class="job-main"><h3>Hairdresser - Analia Franco - São Paulo (SP)</h3><p>SPA BELA VISTA - Posted by SPA BELA VISTA</p></div>
      <div class="job-place">Santo André<small>São Paulo, the Federative Republic of Brazil</small></div>
      <div class="job-date">June 21<small>2013</small></div></li>
    <li class="job"><div class="job-thumb"><div role="img" aria-label="Portrait photo" style="background:linear-gradient(#6a3e2a,#c89070)"></div></div>
      <div class="job-main"><h3>Hairdresser - Analia Franco - São Paulo (SP)</h3><p>SPA BELA VISTA - Posted by SPA BELA VISTA</p></div>
      <div class="job-place">Santo André<small>São Paulo, the Federative Republic of Brazil</small></div>
      <div class="job-date">June 21<small>2013</small></div></li>
  </ul>
</section>
<a class="view-all abs">View All Company Posts ▸</a>

<div class="side-rule abs"></div>
<aside class="vacancies abs">
  <h2>Job Vacancies</h2>
  <ul>
    <li>Assistant Hairdresser</li><li>Assistant Cleaning</li><li>Hairdresser</li><li>Epilator</li>
    <li>Designer Eyebrow</li><li>Featured</li><li>Nurse</li><li>Beautician</li><li>Physiotherapist</li>
    <li>Management / Coordination</li><li>Manicure and Pedicure</li><li>Makeup artist</li>
    <li>Massage therapist</li><li>Other</li>
  </ul>
</aside>
<div class="side-divider abs"></div>

<div class="tabs abs"><span class="tab active">Search by</span><span class="tab alt">Tags</span></div>
<div class="filter-box abs">
  <div>Job Type Job<span>›</span></div>
  <div>Salary Job<span>›</span></div>
  <div>Job Category<span>›</span></div>
  <div>Published Date<span>›</span></div>
</div>

<div class="newsletter abs">
  <h2>Newsletters Subscribe</h2>
  <div class="email">email address</div>
  <div class="subscribe">SUBSCRIBE</div>
</div>

<div class="ad abs" role="img" aria-label="Advertisement banner for a used items marketplace with photos of a car and a motorcycle"></div>

<footer class="site-footer abs">
  <nav class="foot-nav abs"><a>HOME</a><a>BLOG</a><a>FOR BUSINESS</a><a>EVENTS &amp; PARTNERS</a><a>ABOUT US</a><a>CONTACT</a></nav>
  <p class="copyright abs">Copyright © 2013 Company name.  All right reserved</p>
  <div class="social abs"><span></span><span></span><span></span><span></span></div>
</footer>

</body>
</html>
```